New Business Card for our Indoor Golf Training Facility

We are looking for designs for a new business card for our indoor golf training facility. Attached is our logo, our logo with our slogan, and here is our elevator pitch (What makes us different from the others) not sure if all the info will fit on one card, maybe you can condense the elevator pitch? here is the info

Elevator Pitch
We work with serious golfers and those that want to be serious golfers…
to make you better, faster, at all phases of the game…
We use the same state-of-the-art technology as professional golfers…
which produces data sets that shows your improvement in real time.
Our facility is available 24/7 to our members, which allows you to improve on your time.

our website: www.birchpinlinks.com

Target Market(s)

Golfers

Font styles to use
Serif
Sans Serif

Colors
ec1f27
f59195
fbd4d5
919191
d3d3d3
1b1b1b

Requirements
Must have
• our logo or our logo with the slogan, elevator pitch (can be condensed or shortened)

```html
<!DOCTYPE html>
<html lang="en">
<head>
<meta charset="utf-8">
<title>Birch Pin Links – Business Card</title>
<link href="https://fonts.googleapis.com/css2?family=Roboto:wght@400;700;900&family=Roboto+Condensed:wght@400;700&display=swap" rel="stylesheet">
<style>
  :root {
    --red: #ec1f27;
    --red-soft: #f59195;
    --red-pale: #fbd4d5;
    --grey: #919191;
    --grey-light: #d3d3d3;
    --ink: #1b1b1b;
    --paper: #ffffff;
    --backdrop: #ecebe8;
  }
  * { box-sizing: border-box; margin: 0; padding: 0; }
  html, body { width: 1200px; height: 911px; overflow: hidden; background: var(--backdrop); }
  body { position: relative; font-family: "Roboto", sans-serif; color: var(--ink); }

  .card {
    position: absolute; width: 540px; height: 310px; border-radius: 18px;
    background: var(--paper); overflow: hidden;
    box-shadow: 0 6px 18px rgba(0,0,0,0.18);
  }
  .card--front { left: 40px; top: 300px; }
  .card--back { left: 620px; top: 300px; }

  /* front */
  .front-emblem { position: absolute; left: 0; top: 0; width: 540px; height: 310px; }
  .emblem-name {
    font-family: "Roboto", sans-serif; font-weight: 900; font-size: 28px;
    fill: var(--paper); text-anchor: middle;
  }
  .contact { position: absolute; right: 34px; top: 30px; width: 230px; text-align: right; }
  .contact__name { font-family: "Roboto Condensed", sans-serif; font-weight: 700; font-size: 26px; color: var(--red); line-height: 1; }
  .contact__role { font-family: "Roboto Condensed", sans-serif; font-weight: 700; font-size: 14px; color: var(--ink); margin-top: 4px; }
  .contact__rule { border-top: 1px dotted var(--grey); margin: 14px 0 12px; }
  .contact__address { font-size: 13px; line-height: 1.45; color: #444; }
  .contact__lines { list-style: none; font-size: 13px; line-height: 1.6; color: #444; }
  .contact__lines li { display: flex; justify-content: flex-end; align-items: center; gap: 7px; }
  .contact__icon { width: 13px; height: 13px; flex: none; }

  /* back */
  .brand { position: absolute; left: 40px; top: 32px; }
  .brand__row { display: flex; align-items: center; gap: 12px; }
  .brand__dot { width: 40px; height: 40px; border-radius: 50%; border: 4px solid var(--red); }
  .brand__name { font-family: "Roboto", sans-serif; font-weight: 900; font-size: 40px; color: var(--red); letter-spacing: -0.5px; }
  .brand__slogan { font-family: "Roboto Condensed", sans-serif; font-size: 17px; color: var(--red); margin: 4px 0 0 52px; }

  .pitch {
    position: absolute; left: 0; right: 0; bottom: 22px; height: 150px;
    background: var(--red); color: var(--paper); padding: 26px 30px 0;
  }
  .pitch__label {
    position: absolute; left: 230px; top: -14px; background: var(--paper); color: var(--red);
    font-family: "Roboto Condensed", sans-serif; font-weight: 700; font-size: 16px;
    padding: 4px 14px; border-radius: 14px 14px 0 0;
  }
  .pitch__text { font-family: "Roboto Condensed", sans-serif; font-size: 12.5px; line-height: 1.42; text-align: center; }
  .pitch__social { display: flex; justify-content: center; gap: 5px; margin-top: 7px; }
  .pitch__social span { width: 16px; height: 16px; border-radius: 50%; background: var(--paper); }
</style>
</head>
<body>

  <section class="card card--front" aria-label="Business card front">
    <svg class="front-emblem" viewBox="0 0 540 310">
      <rect x="0" y="225" width="300" height="85" fill="var(--red)"/>
      <circle cx="160" cy="188" r="122" fill="var(--paper)"/>
      <circle cx="160" cy="188" r="110" fill="var(--red)"/>
      <text class="emblem-name" x="160" y="198">Birch Pin Links</text>
    </svg>

    <div class="contact">
      <p class="contact__name">Jordan Reyes</p>
      <p class="contact__role">CEO/Founder</p>
      <div class="contact__rule"></div>
      <p class="contact__address">418 W. Alder Ave.<br>Suite B3, Fairhaven<br>OH 45099</p>
      <div class="contact__rule"></div>
      <ul class="contact__lines">
        <li>555-012-3388
          <svg class="contact__icon" viewBox="0 0 16 16"><circle cx="8" cy="8" r="8" fill="var(--red)"/><path d="M5 4.5c.6-.4 1.2 0 1.4.6l.4 1.2c.1.4-.1.7-.4.9l-.4.3c.4 1 1.2 1.8 2.2 2.2l.3-.4c.2-.3.5-.5.9-.4l1.2.4c.6.2 1 .8.6 1.4-.5.8-1.5 1.1-2.4.7C6.6 10.7 5.3 9.4 4.6 7.2c-.4-.9-.1-2 .4-2.7z" fill="var(--paper)"/></svg>
        </li>
        <li>info@birchpinlinks.com
          <svg class="contact__icon" viewBox="0 0 16 16"><circle cx="8" cy="8" r="8" fill="var(--red)"/><rect x="4" y="5.2" width="8" height="5.6" fill="var(--paper)"/><path d="M4 5.2l4 3 4-3" stroke="var(--red)" stroke-width="0.9" fill="none"/></svg>
        </li>
        <li>birchpinlinks.com
          <svg class="contact__icon" viewBox="0 0 16 16"><circle cx="8" cy="8" r="8" fill="var(--red)"/><circle cx="8" cy="8" r="4" fill="none" stroke="var(--paper)" stroke-width="1.1"/><path d="M4 8h8M8 4c-1.6 2.4-1.6 5.6 0 8M8 4c1.6 2.4 1.6 5.6 0 8" stroke="var(--paper)" stroke-width="0.9" fill="none"/></svg>
        </li>
      </ul>
    </div>
  </section>

  <section class="card card--back" aria-label="Business card back">
    <div class="brand">
      <div class="brand__row">
        <span class="brand__dot"></span>
        <span class="brand__name">Birch Pin Links</span>
      </div>
      <p class="brand__slogan">Train Smart. Play Sharp. Go Further.</p>
    </div>

    <div class="pitch">
      <span class="pitch__label">ELEVATOR PITCH:</span>
      <p class="pitch__text">
        We work with serious golfers and those that want to be serious golfers…<br>
        to make you better, faster, at all phases of the game…<br>
        We use the same state-of-the-art technology as professional golfers…<br>
        which produces data sets that shows your improvement in real time.<br>
        Our facility is available 24/7 to our members, which allows you to improve on your time.
      </p>
      <div class="pitch__social"><span></span><span></span></div>
    </div>
  </section>

</body>
</html>
```